QZSTREAMHUB ( Wordpress website for catalogue of Vorlo Stream Pages)

Need a website to showcase different Vorlo Stream pages ( in different categories). Similar to e-commerce except no check-out / purchase of items. Pls use our logos provided and color scheme to be white+red+ blue as per our logo.

Target Market(s)

Consumers

Font styles to use
Sans Serif

Colors
ffffff
ec1f27
3276b5

Requirements
Must have
• I will need a Wordpress Theme as a handover. Also, pls use the color scheme (red+blue+white) as per logo attached. Prefer clean and near design with white space.

```html
<!DOCTYPE html>
<html lang="en">
<head>
<meta charset="utf-8">
<title>QZSTREAMHUB – A Portal of Curated Vorlo Stream Pages</title>
<link href="https://fonts.googleapis.com/css2?family=Roboto:wght@400;500;700;900&family=Roboto+Condensed:wght@700;800&family=Open+Sans:wght@400;600&family=Dancing+Script:wght@700&display=swap" rel="stylesheet">
<style>
:root{
  --red:#ec1f27;
  --blue:#2c5fa8;
  --brand-blue:#3276b5;
  --white:#ffffff;
  --ink:#1d1d1f;
  --text:#2e2e33;
  --soft:#ededf4;
  --line:#cfd0d8;
}
*{margin:0;padding:0;box-sizing:border-box}
html,body{width:1200px;height:2646px;overflow:hidden}
body{position:relative;background:var(--white);font-family:'Roboto',sans-serif;color:var(--text)}
.abs{position:absolute}
a{color:inherit;text-decoration:none}

/* header */
.site-header{position:absolute;left:0;top:0;width:1200px;height:110px;background:var(--white)}
.brand{position:absolute;left:134px;top:26px;display:flex;align-items:center;gap:10px}
.brand-mark{width:22px;height:22px;background:var(--red)}
.brand-name{font-family:'Roboto',sans-serif;font-weight:900;font-size:34px;color:var(--red);letter-spacing:.5px}
.follow{position:absolute;left:733px;top:31px;font-size:11px;font-weight:700;letter-spacing:.5px;color:var(--ink)}
.social-dot{position:absolute;top:25px;width:27px;height:27px;border-radius:50%}
.call-label{position:absolute;left:972px;top:22px;font-size:11px;font-weight:700;color:var(--ink);letter-spacing:.5px}
.call-number{position:absolute;left:972px;top:34px;font-size:22px;font-weight:700;color:var(--brand-blue)}
.main-nav{position:absolute;top:78px;left:0;font-size:14px;font-weight:500;color:var(--ink)}
.main-nav a{position:absolute;white-space:nowrap}
.main-nav .active{color:var(--red);text-decoration:underline;text-underline-offset:3px}

/* hero */
.hero{position:absolute;left:0;top:110px;width:1200px;height:560px;background:var(--soft)}
.hero-title{position:absolute;left:128px;top:30px;font-family:'Roboto Condensed',sans-serif;font-weight:800;font-size:64px;line-height:54px;color:#1a1a1a;letter-spacing:-1.5px}
.hero-of{position:absolute;left:372px;top:40px;font-family:'Dancing Script',cursive;font-size:62px;color:var(--red)}
.hero-live{position:absolute;left:133px;top:224px;background:var(--red);color:var(--white);font-family:'Roboto Condensed',sans-serif;font-weight:800;font-size:56px;line-height:56px;padding:0 12px;border-radius:4px}
.hero-art{position:absolute;left:340px;top:200px;width:860px;height:360px;background:linear-gradient(100deg,#dcdfe9 0%,#c9d3f0 45%,#a9bdf0 75%,#d7def3 100%);border-radius:200px 0 0 0}
.slider-btn{position:absolute;top:430px;width:38px;height:38px;background:var(--blue);display:flex;align-items:center;justify-content:center}

/* quick links */
.quick{position:absolute;top:726px;width:179px;height:142px;border:1px solid var(--line);border-radius:6px;background:var(--white);text-align:center}
.quick svg{margin-top:28px}
.quick span{position:absolute;left:0;right:0;top:99px;font-size:14px;font-weight:500;color:var(--ink)}

/* welcome */
.welcome{position:absolute;left:0;top:915px;width:1200px;height:453px;background:var(--soft)}
.collage{position:absolute;left:134px;top:46px;width:460px;height:355px;background:linear-gradient(135deg,#6b2a22,#c8633b 40%,#5a7a3a 80%,#2f5e22);border:3px solid #111}
.welcome-kicker{position:absolute;left:634px;top:50px;font-size:18px;color:var(--ink)}
.welcome-title{position:absolute;left:634px;top:72px;font-size:38px;color:var(--ink);letter-spacing:1px}
.welcome-lead{position:absolute;left:636px;top:128px;width:420px;font-size:14px;line-height:20px;color:var(--ink)}
.tag{position:absolute;left:640px;background:var(--red);color:var(--white);font-size:12px;font-weight:700;padding:3px 9px;letter-spacing:.4px}
.welcome-text{position:absolute;left:640px;width:430px;font-family:'Open Sans',sans-serif;font-size:13px;line-height:17.5px;color:var(--ink)}

/* reviews */
.reviews{position:absolute;left:0;top:1368px;width:1200px;height:402px;background:var(--blue)}
.section-title{position:absolute;left:0;width:1200px;text-align:center;font-size:23px;font-weight:700;letter-spacing:.5px}
.title-rule{position:absolute;left:585px;width:31px;height:3px}
.review-card{position:absolute;top:124px;width:458px;height:226px;background:var(--white);border-radius:6px}
.review-photo{position:absolute;left:4px;top:28px;width:170px;height:140px;border-radius:4px}
.stars{position:absolute;left:191px;top:30px;color:var(--red);font-size:14px;letter-spacing:1px}
.review-head{position:absolute;left:191px;top:51px;font-size:13px;color:var(--ink)}
.review-body{position:absolute;left:192px;top:85px;width:245px;font-family:'Open Sans',sans-serif;font-size:12px;line-height:16px;color:var(--ink)}
.review-name{position:absolute;left:195px;top:184px;font-size:13px;color:var(--ink)}
.rv-arrow{position:absolute;top:1590px}

/* blog */
.blog-card{position:absolute;top:1893px;width:295px;height:342px;background:var(--white);box-shadow:0 2px 10px rgba(0,0,0,.13)}
.blog-photo{width:295px;height:184px}
.blog-title{position:absolute;left:22px;top:206px;font-size:15px;font-weight:700;color:var(--ink);letter-spacing:.3px}
.blog-text{position:absolute;left:22px;top:236px;width:255px;font-family:'Open Sans',sans-serif;font-size:12px;line-height:16px;color:var(--ink)}
.read-more{position:absolute;left:22px;top:300px;font-size:11px;font-weight:700;color:var(--red);text-decoration:underline}

/* footer */
.site-footer{position:absolute;left:0;top:2286px;width:1200px;height:360px;background:var(--blue);color:var(--white)}
.footer-brand{position:absolute;left:134px;top:88px;display:flex;align-items:center;gap:12px}
.footer-brand .brand-mark{background:var(--white);width:26px;height:26px}
.footer-brand .brand-name{color:var(--white);font-size:38px}
.f-head{position:absolute;top:50px;font-size:13px;font-weight:700;letter-spacing:.3px}
.f-menu{position:absolute;left:513px;top:88px;font-size:12px;line-height:20px}
.f-item{position:absolute;font-size:11.5px;line-height:16px}
.f-icon{position:absolute;width:24px;height:24px;border-radius:50%;background:var(--white);display:flex;align-items:center;justify-content:center}
.f-rule{position:absolute;left:134px;top:266px;width:934px;height:1px;background:rgba(255,255,255,.25)}
.copyright{position:absolute;left:0;width:1200px;top:308px;text-align:center;font-size:10px}
</style>
</head>
<body>

<header class="site-header">
  <a class="brand" href="#"><span class="brand-mark"></span><span class="brand-name">QZSTREAMHUB</span></a>
  <span class="follow">FOLLOW US</span>
  <span class="social-dot" style="left:815px;background:#3b5ba6"></span>
  <span class="social-dot" style="left:849px;background:#1da1f2"></span>
  <span class="social-dot" style="left:883px;background:#1d2a5a"></span>
  <svg class="abs" style="left:935px;top:28px" width="28" height="28" viewBox="0 0 24 24" fill="none" stroke="#3276b5" stroke-width="1.6"><path d="M5 3h4l2 5-2.5 1.5a11 11 0 0 0 6 6L16 13l5 2v4a2 2 0 0 1-2 2A16 16 0 0 1 3 5a2 2 0 0 1 2-2z"/><path d="M15 3a6 6 0 0 1 6 6M15 7a2 2 0 0 1 2 2"/></svg>
  <span class="call-label">CALL US</span>
  <span class="call-number">9000 4821</span>
  <nav class="main-nav">
    <a class="active" style="left:660px" href="#">HOME</a>
    <a style="left:739px" href="#">ABOUT</a>
    <a style="left:824px" href="#">SERVICES</a>
    <a style="left:925px" href="#">SHOP</a>
    <a style="left:1001px" href="#">CONTACT</a>
  </nav>
</header>

<section class="hero">
  <div class="hero-art" role="img" aria-label="Illustration of a phone showing a live stream of dresses beside two shoppers with bags, groceries and a clothes rack"></div>
  <h1 class="hero-title">A PORTAL<br>CURATED<br>VORLO</h1>
  <span class="hero-of">Of</span>
  <span class="hero-live">STREAM</span>
  <a class="slider-btn" style="left:134px" href="#"><svg width="14" height="14" viewBox="0 0 14 14"><path d="M9 2 4 7l5 5" stroke="#fff" stroke-width="2" fill="none"/></svg></a>
  <a class="slider-btn" style="left:181px" href="#"><svg width="14" height="14" viewBox="0 0 14 14"><path d="M5 2l5 5-5 5" stroke="#fff" stroke-width="2" fill="none"/></svg></a>
</section>

<a class="quick" style="left:134px" href="#">
  <svg width="48" height="48" viewBox="0 0 48 48" fill="none" stroke="#3276b5" stroke-width="3"><path d="M4 18h40l-4 24H8z"/><path d="M14 18 22 6M34 18 26 6M14 26v10M20 26v10M28 26v10M34 26v10"/></svg>
  <span>ORDERS</span></a>
<a class="quick" style="left:323px" href="#">
  <svg width="52" height="48" viewBox="0 0 52 48" fill="#3276b5"><path d="M4 18h10l20-12v34L14 28H4z"/><path d="M10 30h8l3 12h-8z"/><path d="M40 16l8-5M41 23h9M40 30l8 5" stroke="#3276b5" stroke-width="3"/></svg>
  <span>PROMOS</span></a>
<a class="quick" style="left:511px" href="#">
  <svg width="48" height="48" viewBox="0 0 48 48" fill="none" stroke="#3276b5" stroke-width="3"><circle cx="24" cy="17" r="13"/><circle cx="24" cy="17" r="6"/><path d="M14 27 8 40l7-1 4 6 5-12 5 12 4-6 7 1-6-13"/></svg>
  <span>REWARDS</span></a>
<a class="quick" style="left:700px" href="#">
  <svg width="48" height="48" viewBox="0 0 48 48" fill="#3276b5"><path d="M10 6h8l4 10-5 4a22 22 0 0 0 11 11l4-5 10 4v8a4 4 0 0 1-4 4A34 34 0 0 1 6 10a4 4 0 0 1 4-4z"/><path d="M30 6a12 12 0 0 1 12 12M30 13a5 5 0 0 1 5 5" stroke="#3276b5" stroke-width="3" fill="none"/></svg>
  <span>CALL US</span></a>
<a class="quick" style="left:889px" href="#">
  <svg width="50" height="50" viewBox="0 0 50 50" fill="none" stroke="#3276b5" stroke-width="2.6"><path d="M4 14l12-4 16 6 14-5v32l-14 5-16-6-12 4z"/><path d="M16 10v32M32 16v32"/><circle cx="13" cy="12" r="5"/><path d="M13 17v6"/><circle cx="37" cy="27" r="6"/></svg>
  <span>DIRECTION</span></a>

<section class="welcome">
  <div class="collage" role="img" aria-label="Grid of frozen food promotion posters with prices and bundles"></div>
  <p class="welcome-kicker">WELCOME TO</p>
  <h2 class="welcome-title">QZSTREAMHUB</h2>
  <p class="welcome-lead">FROSTLINE SEEKS TO PROVIDE THE BEST QUALITY OF FROZEN SUPPLIES IN SINGAPORE</p>
  <span class="tag" style="top:195px">MISSION</span>
  <p class="welcome-text" style="top:231px">To continuously strive in improving the quality of our frozen products while keeping prices competitive and to provide an excellent customer experience to foster long-term engagement</p>
  <span class="tag" style="top:297px">VISION</span>
  <p class="welcome-text" style="top:333px">To be the leading frozen food supplier being everyone’s choice for quality food products. We believe that our business is as important as our customers’ businesses. Hence, only by achieving customer’s satisfaction, can we truly experience success.</p>
</section>

<section class="reviews">
  <h2 class="section-title" style="top:42px;color:var(--white)">REVIEWS</h2>
  <span class="title-rule" style="top:80px;background:var(--white)"></span>
  <article class="review-card" style="left:135px">
    <div class="review-photo" role="img" aria-label="Product photo of a computer motherboard" style="background:linear-gradient(135deg,#e8eef6,#4a7cc0 50%,#1e3c78)"></div>
    <span class="stars">★★★★★</span>
    <h3 class="review-head">LOREM IPSUM IS SIMPLY DUMMY TEXT</h3>
    <p class="review-body">There are many variations of passages of Lorem Ipsum available, but the majority have suffered alteration in some form, by injected humour, or randomised words which don't look even slightly believable</p>
    <span class="review-name">RICHARD</span>
  </article>
  <article class="review-card" style="left:607px">
    <div class="review-photo" role="img" aria-label="Product photo of a loudspeaker driver" style="background:radial-gradient(circle at 50% 50%,#555 0,#111 40%,#9a9a9a 58%,#fff 62%)"></div>
    <span class="stars">★★★★★</span>
    <h3 class="review-head">LOREM IPSUM IS SIMPLY DUMMY TEXT</h3>
    <p class="review-body">There are many variations of passages of Lorem Ipsum available, but the majority have suffered alteration in some form, by injected humour, or randomised words which don't look even slightly believable</p>
    <span class="review-name">RICHARD</span>
  </article>
  <svg class="abs" style="left:82px;top:204px" width="20" height="30" viewBox="0 0 20 30"><path d="M16 3 4 15l12 12" stroke="#fff" stroke-width="3" fill="none"/></svg>
  <svg class="abs" style="left:1098px;top:204px" width="20" height="30" viewBox="0 0 20 30"><path d="M4 3l12 12L4 27" stroke="#fff" stroke-width="3" fill="none"/></svg>
</section>

<h2 class="section-title" style="top:1813px;color:var(--ink)">LATEST BLOG</h2>
<span class="title-rule" style="top:1850px;background:var(--red)"></span>

<article class="blog-card" style="left:134px">
  <div class="blog-photo" role="img" aria-label="Store shelf of boxed kitchen appliances and an air fryer" style="background:linear-gradient(135deg,#cfd3dc,#8a7ab0 45%,#3a3a44 75%,#c9b488)"></div>
  <h3 class="blog-title">AT VERO EOS ET ACCUSAMUS</h3>
  <p class="blog-text">Sed ut perspiciatis unde omnis iste natus error sit voluptatem accusantium dolor emque laudantiumtotam rem.</p>
  <a class="read-more" href="#">READ MORE</a>
</article>
<article class="blog-card" style="left:452px">
  <div class="blog-photo" role="img" aria-label="Grid of boxed fresh fruit including tomatoes, grapes and mangoes" style="background:linear-gradient(135deg,#c8d48a,#c8322a 35%,#8a9c3a 60%,#d84a2a)"></div>
  <h3 class="blog-title">AT VERO EOS ET ACCUSAMUS</h3>
  <p class="blog-text">Sed ut perspiciatis unde omnis iste natus error sit voluptatem accusantium dolor emque laudantiumtotam rem.</p>
  <a class="read-more" href="#">READ MORE</a>
</article>
<article class="blog-card" style="left:769px">
  <div class="blog-photo" role="img" aria-label="Warehouse shelves stacked with boxed home goods" style="background:linear-gradient(135deg,#5a5650,#b8b2a6 45%,#e4e0d8 70%,#8a8276)"></div>
  <h3 class="blog-title">AT VERO EOS ET ACCUSAMUS</h3>
  <p class="blog-text">Sed ut perspiciatis unde omnis iste natus error sit voluptatem accusantium dolor emque laudantiumtotam rem.</p>
  <a class="read-more" href="#">READ MORE</a>
</article>

<footer class="site-footer">
  <a class="footer-brand" href="#"><span class="brand-mark"></span><span class="brand-name">QZSTREAMHUB</span></a>

  <h4 class="f-head" style="left:513px">MENU</h4>
  <nav class="f-menu"><a href="#">HOME</a><br><a href="#">ABOUT</a><br><a href="#">SERVICES</a><br><a href="#">SHOP</a><br><a href="#">CONTACT</a></nav>

  <h4 class="f-head" style="left:700px">CONTACT US</h4>
  <span class="f-icon" style="left:699px;top:89px"><svg width="12" height="12" viewBox="0 0 12 12" fill="#2c5fa8"><path d="M6 0a4 4 0 0 1 4 4c0 3-4 8-4 8S2 7 2 4a4 4 0 0 1 4-4z"/><circle cx="6" cy="4" r="1.5" fill="#fff"/></svg></span>
  <p class="f-item" style="left:731px;top:90px">48 Harbour Lane,<br>Eastvale</p>
  <span class="f-icon" style="left:699px;top:142px"><svg width="12" height="12" viewBox="0 0 24 24" fill="#2c5fa8"><path d="M5 2h4l2 5-3 2a12 12 0 0 0 7 7l2-3 5 2v4a2 2 0 0 1-2 2A18 18 0 0 1 3 4a2 2 0 0 1 2-2z"/></svg></span>
  <p class="f-item" style="left:731px;top:142px">Call Us<br>800.555.0142</p>
  <span class="f-icon" style="left:699px;top:191px"><svg width="12" height="10" viewBox="0 0 12 10" fill="#2c5fa8"><rect width="12" height="10" rx="1"/><path d="M1 1l5 4 5-4" stroke="#fff" fill="none"/></svg></span>
  <p class="f-item" style="left:731px;top:191px">E mail Us<br>info@QZSTREAMHUB.com</p>

  <h4 class="f-head" style="left:963px">FOLLOW US</h4>
  <span class="f-icon" style="left:962px;top:89px"></span>
  <p class="f-item" style="left:997px;top:90px">Like us on<br>VORLO</p>
  <span class="f-icon" style="left:962px;top:142px"></span>
  <p class="f-item" style="left:997px;top:140px">Follow us on<br>CHIRPA</p>
  <span class="f-icon" style="left:962px;top:191px"></span>
  <p class="f-item" style="left:997px;top:190px">Follow us on<br>LINKORA</p>

  <span class="f-rule"></span>
  <p class="copyright">Copyright © 2020 All Rights Reserved</p>
</footer>

</body>
</html>
```